Roofing Company Modern look

I want a modern and sophisticated look for our roofing business.

Our address is :

5217 Mallow Creek Ln
Cedar Bay, Fl 32190

(407)-583-2196

www.HarborlineRoofsFl.com

I also want to make sure on the back there is a spot to put
Project Manager Name :

Number:

Because the cards will be used by all sales people

Project Manager Name :

Also there are accreditation we have logos are uploaded here as well that I would like maybe on the back of card as well

I also want to highlight our special attributions or trades:

Residential & Commercial
Fully Insured
License # CCC7482913
Insurance Claims
Serving Central Florida Since 1992
Free Estimates

Contact Information for Business Card

Our address is :

5217 Mallow Creek Ln
Cedar Bay, Fl 32190

(407)-583-2196

Project Manager Name :

Residential & Commercial
Fully Insured
License # CCC7482913
Insurance Claims
Free Estimates

Font styles to use
Serif
Sans Serif

Colors
3176b5

Requirements
Must have
• Must have royal blue like my logo grey and black are the colors I like

```html
<!DOCTYPE html>
<html lang="en">
<head>
<meta charset="utf-8">
<title>Harborline Roofs – Business Card</title>
<link rel="stylesheet" href="https://fonts.googleapis.com/css2?family=Lato:wght@400;700&family=Montserrat:wght@500;600&display=swap">
<style>
:root{
  --royal:#3176b5;
  --ink:#0b0b0c;
  --grey:#555a60;
  --text:#4a4d52;
  --paper:#ffffff;
  --paper-soft:#f4f5f7;
  --stage:#2c2c2e;
  --badge:#c9ccd1;
}
*{margin:0;padding:0;box-sizing:border-box}
html,body{width:1200px;height:1192px;overflow:hidden;background:var(--stage)}
.card{position:absolute;left:209px;width:782px;height:450px;border-radius:14px;overflow:hidden}
.card-front{top:130px;background:var(--paper);font-family:"Lato",sans-serif;color:var(--text)}
.brand{position:absolute;left:70px;top:200px;width:300px;display:flex;align-items:center;gap:12px}
.brand-dot{width:22px;height:22px;border-radius:50%;background:var(--royal);flex:none}
.brand-name{font-family:"Lato",sans-serif;font-weight:700;font-size:30px;color:var(--royal);white-space:nowrap}
.divider{position:absolute;left:390px;top:111px;width:2px;height:226px;background:var(--royal)}
.details{position:absolute;left:409px;top:108px;font-size:19px;line-height:22px;white-space:nowrap}
.person{font-size:25px;line-height:26px;font-weight:700;color:var(--grey)}
.person .first{color:var(--royal)}
.role{margin-bottom:6px}
.accent{color:var(--royal)}
.dash{width:11px;height:2px;background:var(--royal);margin:4px 0 6px}
.contact{display:flex;align-items:center;gap:9px}
.contact svg{width:14px;height:14px;flex:none;fill:var(--royal)}
.highlights{position:absolute;left:0;right:0;top:380px;display:flex;justify-content:center;align-items:center;gap:9px;font-size:17px}
.highlights i{width:8px;height:8px;border-radius:50%;background:var(--royal);display:block}

.card-back{top:614px;background:var(--paper-soft);font-family:"Montserrat",sans-serif}
.back-top{position:absolute;left:0;top:0;width:100%;height:331px;background:var(--ink)}
.back-brand{position:absolute;left:0;right:0;top:140px;display:flex;justify-content:center;align-items:center;gap:14px}
.back-brand .brand-name{font-size:40px}
.back-web{position:absolute;left:0;right:0;top:287px;text-align:center;color:#fff;font-size:21px;font-weight:500;letter-spacing:1.5px}
.rule{position:absolute;left:0;top:331px;width:100%;height:3px;background:var(--royal)}
.pill{position:absolute;left:224px;top:322px;width:333px;height:22px;border-radius:11px;background:var(--royal);color:#fff;font-size:19px;font-weight:500;text-align:center;line-height:22px}
.badges{position:absolute;left:0;top:364px;width:100%;height:66px}
.badge{position:absolute;background:var(--badge)}
.badge-a{left:167px;top:0;width:51px;height:66px;border-radius:4px}
.badge-b{left:254px;top:4px;width:75px;height:58px;clip-path:polygon(50% 0,100% 18%,100% 82%,50% 100%,0 82%,0 18%)}
.badge-c{left:369px;top:13px;width:141px;height:40px}
.badge-d{left:538px;top:0;width:66px;height:66px;border-radius:50%}
</style>
</head>
<body>
<section class="card card-front" aria-label="Card front">
  <div class="brand"><span class="brand-dot"></span><span class="brand-name">Harborline Roofs</span></div>
  <div class="divider"></div>
  <div class="details">
    <div class="person"><span class="first">Dana</span> Whitcomb</div>
    <div class="role">Project Manager</div>
    <div><span class="accent">License #</span> CCC7482913</div>
    <div>Residential &amp; Commercial</div>
    <div class="dash"></div>
    <div>5217 Mallow Creek Ln</div>
    <div>Cedar Bay, Fl 32190</div>
    <div class="dash"></div>
    <div class="contact"><svg viewBox="0 0 24 24"><path d="M6.6 10.8a15.1 15.1 0 0 0 6.6 6.6l2.2-2.2a1 1 0 0 1 1-.25 11.4 11.4 0 0 0 3.6.6 1 1 0 0 1 1 1V20a1 1 0 0 1-1 1A17 17 0 0 1 3 4a1 1 0 0 1 1-1h3.5a1 1 0 0 1 1 1 11.4 11.4 0 0 0 .6 3.6 1 1 0 0 1-.25 1z"/></svg>(407)-583-2196</div>
    <div class="contact"><svg viewBox="0 0 24 24"><path d="M2 5h20l-10 7z"/><path d="M2 7.5l10 7 10-7V19H2z"/></svg>HarborlineRoofsFl@mailbox.com</div>
    <div class="contact"><svg viewBox="0 0 24 24"><circle cx="12" cy="12" r="10"/></svg>www.HarborlineRoofsFl.com</div>
  </div>
  <div class="highlights">
    <span>Fully Insured</span><i></i>
    <span>Insurance Claims</span><i></i>
    <span>Serving Central Florida Since 1992</span><i></i>
    <span>Free Estimates</span>
  </div>
</section>

<section class="card card-back" aria-label="Card back">
  <div class="back-top"></div>
  <div class="back-brand"><span class="brand-dot"></span><span class="brand-name">Harborline Roofs</span></div>
  <div class="back-web">www.harborlineroofsfl.com</div>
  <div class="rule"></div>
  <div class="pill">Our Accreditations &amp; Partners</div>
  <div class="badges">
    <div class="badge badge-a" role="img" aria-label="Accreditation badge"></div>
    <div class="badge badge-b" role="img" aria-label="Shingle applicator certificate badge"></div>
    <div class="badge badge-c" role="img" aria-label="Authorized contractor badge"></div>
    <div class="badge badge-d" role="img" aria-label="Screened and approved listing badge"></div>
  </div>
</section>
</body>
</html>
```